Gobal construction supply company needs new business card design

I need a business card design for my global supply company using an existing logo. i will be looking to print these on rounded corner cards with the black background version of my logo on the back. on the front white background, my logo again and my simple details.

```html
<!DOCTYPE html>
<html lang="en">
<head>
<meta charset="utf-8">
<title>Coastline Build Supply – Business Cards</title>
<link rel="stylesheet" href="https://fonts.googleapis.com/css2?family=Montserrat:wght@600;700&family=Roboto:wght@400&display=swap">
<style>
  :root {
    --backdrop: #2e2e2e;
    --card-white: #f4f4f4;
    --card-black: #1c1c1c;
    --ink: #111111;
    --accent-red: #d40000;
    --text-grey: #555555;
    --white: #ffffff;
  }
  * { margin: 0; padding: 0; box-sizing: border-box; }
  html, body {
    width: 1200px; height: 960px; overflow: hidden;
    background: var(--backdrop);
  }
  .canvas { position: relative; width: 1200px; height: 960px; }

  .card {
    position: absolute; width: 600px; height: 342px;
    border-radius: 22px; overflow: hidden;
  }
  .card--front { left: 186px; top: 113px; background: var(--card-white); }
  .card--back { left: 434px; top: 512px; background: var(--card-black); }

  /* Front */
  .brand-front {
    position: absolute; left: 30px; top: 150px; width: 245px;
    display: flex; align-items: center; justify-content: center; gap: 8px;
    font-family: "Montserrat", sans-serif; font-weight: 700;
    font-size: 16px; color: var(--ink); letter-spacing: 0.2px;
    white-space: nowrap;
  }
  .brand-dot {
    width: 14px; height: 14px; border-radius: 50%;
    background: var(--accent-red); flex: none;
  }
  .divider-top {
    position: absolute; left: 309px; top: 0; width: 24px; height: 51px;
    background: var(--accent-red);
  }
  .divider-bar {
    position: absolute; left: 309px; top: 125px; width: 24px; height: 217px;
    background: var(--ink);
  }
  .person-name {
    position: absolute; left: 312px; top: 60px;
    font-family: "Montserrat", sans-serif; font-weight: 700;
    font-size: 28px; color: var(--ink); letter-spacing: 0.5px;
  }
  .person-title {
    position: absolute; left: 312px; top: 94px;
    font-family: "Montserrat", sans-serif; font-weight: 700;
    font-size: 16px; color: var(--accent-red);
  }
  .contact-icon {
    position: absolute; left: 311px; width: 20px; height: 20px;
  }
  .contact-block {
    position: absolute; left: 353px;
    font-family: "Roboto", sans-serif; font-size: 15px; line-height: 19px;
    color: var(--text-grey);
  }
  .contact-block--address { top: 158px; }
  .contact-block--phone { top: 214px; }
  .contact-block--web { top: 265px; }
  .icon--address { top: 165px; }
  .icon--phone { top: 223px; }
  .icon--web { top: 273px; }

  /* Back */
  .brand-back {
    position: absolute; left: 0; top: 130px; width: 600px;
    display: flex; align-items: center; justify-content: center; gap: 14px;
    font-family: "Montserrat", sans-serif; font-weight: 700;
    font-size: 32px; color: var(--card-white); white-space: nowrap;
  }
  .brand-square {
    width: 30px; height: 30px; background: var(--accent-red); flex: none;
  }
  .band-red {
    position: absolute; left: 0; top: 285px; width: 145px; height: 30px;
    background: var(--accent-red);
  }
  .band-web {
    position: absolute; left: 229px; top: 285px; width: 371px; height: 30px;
    background: var(--white);
    display: flex; align-items: center; justify-content: center;
    font-family: "Roboto", sans-serif; font-size: 15px;
    letter-spacing: 3px; color: var(--ink);
  }
</style>
</head>
<body>
<div class="canvas">

  <section class="card card--front">
    <div class="brand-front"><span>COASTLINE BUILD SUPPLY</span><span class="brand-dot"></span></div>

    <div class="divider-top"></div>
    <div class="divider-bar"></div>

    <h1 class="person-name">DANIEL HARTLEY</h1>
    <p class="person-title">CEO/FOUNDER</p>

    <svg class="contact-icon icon--address" viewBox="0 0 20 20" aria-hidden="true">
      <circle cx="10" cy="10" r="10" fill="#d40000"/>
      <path d="M10 4.5a3.6 3.6 0 0 0-3.6 3.6c0 2.7 3.6 7 3.6 7s3.6-4.3 3.6-7A3.6 3.6 0 0 0 10 4.5z" fill="#fff"/>
      <circle cx="10" cy="8.1" r="1.4" fill="#d40000"/>
    </svg>
    <div class="contact-block contact-block--address">4210 Harbor Row<br>Portfield, Westland 20418</div>

    <svg class="contact-icon icon--phone" viewBox="0 0 20 20" aria-hidden="true">
      <circle cx="10" cy="10" r="10" fill="#d40000"/>
      <rect x="6.8" y="4.5" width="6.4" height="11" rx="1.2" fill="#fff"/>
      <rect x="7.8" y="6" width="4.4" height="7" fill="#d40000"/>
    </svg>
    <div class="contact-block contact-block--phone">555 201 4473<br>555 388 0916</div>

    <svg class="contact-icon icon--web" viewBox="0 0 20 20" aria-hidden="true">
      <circle cx="10" cy="10" r="10" fill="#d40000"/>
      <rect x="5" y="6.5" width="10" height="7" rx="0.8" fill="#fff"/>
      <path d="M5.3 7l4.7 3.6L14.7 7" fill="none" stroke="#d40000" stroke-width="1"/>
    </svg>
    <div class="contact-block contact-block--web">daniel@coastlinebuild.com<br>www.coastlinebuild.com</div>
  </section>

  <section class="card card--back">
    <div class="brand-back"><span>COASTLINE BUILD SUPPLY</span><span class="brand-square"></span></div>
    <div class="band-red"></div>
    <div class="band-web">www.coastlinebuild.com</div>
  </section>

</div>
</body>
</html>
```